I need a design that promotes "A peak path hub for runners". services include assessment, massage, physiotherapy, pilates, suspension training, kinesiotaping in any combination.
I would like to bring the design into my website, flyers etc

Target Market(s)

athletes from beginner to elite - any age, male and female

Industry/Entity Type

Shop

Contact Information for Business Card

Peak-Path Hub for Runners
17 Corla Lane, Westmere, Tauranga
021 874 3061
tess.harlow@mailbrook.example

Logo Text

Logo styles of interest
Abstract Logo
Requirements
Nice to have
• Blue colour theme

```html
<!DOCTYPE html>
<html lang="en">
<head>
<meta charset="utf-8">
<title>Peak-Path Hub for Runners – Services</title>
<link href="https://fonts.googleapis.com/css2?family=Open+Sans:wght@400&display=swap" rel="stylesheet">
<style>
  :root {
    --blue: #41bfff;
    --black: #000000;
    --white: #ffffff;
  }
  * { box-sizing: border-box; margin: 0; padding: 0; }
  html, body { width: 1200px; height: 1000px; overflow: hidden; background: var(--white); }
  body { position: relative; font-family: "Open Sans", Arial, sans-serif; }

  .card {
    position: absolute;
    border-radius: 20px;
    overflow: hidden;
    background: var(--card-bg);
  }

  .brand-name {
    position: absolute;
    left: 40px;
    top: 50%;
    transform: translateY(-50%);
    width: 220px;
    color: var(--name);
    font-size: 28px;
    font-weight: 400;
    line-height: 38px;
  }

  .services {
    position: absolute;
    top: 64px;
    display: flex;
  }
  .services-label {
    display: flex;
    flex-direction: column;
    align-items: center;
    width: 20px;
    color: var(--label);
    font-size: 20px;
    line-height: 24.3px;
  }
  .services-rule {
    width: 2px;
    height: 192px;
    margin: 2px 9px 0 12px;
    background: var(--rule);
  }
  .services-list {
    list-style: none;
    color: var(--list);
    font-size: 18.5px;
    line-height: 27.3px;
    white-space: nowrap;
  }

  .card--night  { left: 20px;  top: 2px;   width: 546px; height: 315px;
    --card-bg: var(--black); --name: var(--blue);
    --label: var(--white); --list: var(--blue); --rule: var(--blue); }
  .card--sky    { left: 627px; top: 5px;   width: 559px; height: 320px;
    --card-bg: var(--blue); --name: var(--white);
    --label: var(--white); --list: var(--white); --rule: var(--white); }
  .card--ink    { left: 20px;  top: 333px; width: 548px; height: 313px;
    --card-bg: var(--blue); --name: var(--black);
    --label: var(--white); --list: var(--black); --rule: var(--white); }
  .card--shadow { left: 627px; top: 333px; width: 559px; height: 323px;
    --card-bg: var(--blue); --name: var(--white);
    --label: var(--white); --list: var(--white); --rule: var(--white); }
  .card--line   { left: 20px;  top: 659px; width: 555px; height: 317px;
    --card-bg: var(--blue); --name: var(--black);
    --label: var(--black); --list: var(--white); --rule: var(--black); }
  .card--light  { left: 627px; top: 663px; width: 559px; height: 322px;
    --card-bg: var(--white); --name: var(--blue);
    --label: var(--blue); --list: var(--blue); --rule: var(--blue); }

  .card--night .services  { left: 303px; }
  .card--sky .services    { left: 313px; top: 68px; }
  .card--ink .services    { left: 307px; }
  .card--shadow .services { left: 313px; top: 68px; }
  .card--line .services   { left: 312px; top: 66px; }
  .card--light .services  { left: 310px; top: 68px; }
</style>
</head>
<body>

<section class="card card--night">
  <p class="brand-name">Peak-Path Hub for Runners</p>
  <div class="services">
    <div class="services-label"><span>s</span><span>e</span><span>r</span><span>v</span><span>i</span><span>c</span><span>e</span><span>s</span></div>
    <div class="services-rule"></div>
    <ul class="services-list">
      <li>Assessment</li><li>Massage</li><li>Physiotherapy</li><li>Pilates</li>
      <li>Suspension training</li><li>Kinesiotaping</li><li>in any combination.</li>
    </ul>
  </div>
</section>

<section class="card card--sky">
  <p class="brand-name">Peak-Path Hub for Runners</p>
  <div class="services">
    <div class="services-label"><span>s</span><span>e</span><span>r</span><span>v</span><span>i</span><span>c</span><span>e</span><span>s</span></div>
    <div class="services-rule"></div>
    <ul class="services-list">
      <li>Assessment</li><li>Massage</li><li>Physiotherapy</li><li>Pilates</li>
      <li>Suspension training</li><li>Kinesiotaping</li><li>in any combination.</li>
    </ul>
  </div>
</section>

<section class="card card--ink">
  <p class="brand-name">Peak-Path Hub for Runners</p>
  <div class="services">
    <div class="services-label"><span>s</span><span>e</span><span>r</span><span>v</span><span>i</span><span>c</span><span>e</span><span>s</span></div>
    <div class="services-rule"></div>
    <ul class="services-list">
      <li>Assessment</li><li>Massage</li><li>Physiotherapy</li><li>Pilates</li>
      <li>Suspension training</li><li>Kinesiotaping</li><li>in any combination.</li>
    </ul>
  </div>
</section>

<section class="card card--shadow">
  <p class="brand-name">Peak-Path Hub for Runners</p>
  <div class="services">
    <div class="services-label"><span>s</span><span>e</span><span>r</span><span>v</span><span>i</span><span>c</span><span>e</span><span>s</span></div>
    <div class="services-rule"></div>
    <ul class="services-list">
      <li>Assessment</li><li>Massage</li><li>Physiotherapy</li><li>Pilates</li>
      <li>Suspension training</li><li>Kinesiotaping</li><li>in any combination.</li>
    </ul>
  </div>
</section>

<section class="card card--line">
  <p class="brand-name">Peak-Path Hub for Runners</p>
  <div class="services">
    <div class="services-label"><span>s</span><span>e</span><span>r</span><span>v</span><span>i</span><span>c</span><span>e</span><span>s</span></div>
    <div class="services-rule"></div>
    <ul class="services-list">
      <li>Assessment</li><li>Massage</li><li>Physiotherapy</li><li>Pilates</li>
      <li>Suspension training</li><li>Kinesiotaping</li><li>in any combination.</li>
    </ul>
  </div>
</section>

<section class="card card--light">
  <p class="brand-name">Peak-Path Hub for Runners</p>
  <div class="services">
    <div class="services-label"><span>s</span><span>e</span><span>r</span><span>v</span><span>i</span><span>c</span><span>e</span><span>s</span></div>
    <div class="services-rule"></div>
    <ul class="services-list">
      <li>Assessment</li><li>Massage</li><li>Physiotherapy</li><li>Pilates</li>
      <li>Suspension training</li><li>Kinesiotaping</li><li>in any combination.</li>
    </ul>
  </div>
</section>

</body>
</html>
```